Business Card Re-Design/Update

We'd like to update out business cards. I've included our current "Style guide" which has the colour scheme of the organisation in it. I've also included the branding files with logos etc in them.

I've also included a copy of one of our existing cards so that you can see how ugly/dated they look. I'd like a fresh modern corporate look.

Target Market(s)

These are for our clients, potential clients, industry contacts - like all business cards

Contact Information for Business Card

Name
Position
Company Address - Level 1, 47 Fernby Street, Carlow Qld 4072
Direct Phone
mobile
Email
Website -www.korvalit.com.au
Logo

Colors

Designer to choose colors to be used in the design.

Requirements
Must have
• Main Logo
• Cards will need to be editable to be able to personalize them for each new employee.
Nice to have
• The MapOut, ShipWell, KeepSteady would be okay to have if they can be sensibly and professionally added to the look without detracting from the main imagery.
• Maybe they could go on the back of the card? will leave this to your creative discretion as to whether/where they fit.
Should not have
• Should not have decorative or script fonts

```html
<!DOCTYPE html>
<html lang="en">
<head>
<meta charset="utf-8">
<title>Korvalit Business Card</title>
<link href="https://fonts.googleapis.com/css2?family=Arimo:wght@400;700&display=swap" rel="stylesheet">
<style>
  :root {
    --backdrop: #d9d9d9;
    --card: #ffffff;
    --ink: #2f2f33;
    --brand-red: #d7161d;
    --faint: #ececec;
    --rule: #8a8a8a;
    --ship-blue: #1f8ad0;
    --keep-magenta: #b51a8e;
    --map-green: #5aa83a;
  }
  * { margin: 0; padding: 0; box-sizing: border-box; }
  html, body { width: 1000px; height: 1200px; overflow: hidden; }
  body {
    background: var(--backdrop);
    font-family: "Arimo", Arial, sans-serif;
    color: var(--ink);
    position: relative;
  }
  .card {
    position: absolute;
    left: 214px;
    width: 578px;
    height: 356px;
    background: var(--card);
    overflow: hidden;
    box-shadow: 0 2px 6px rgba(0,0,0,0.25);
  }
  .card--front { top: 219px; border-radius: 0 62px 0 62px; }
  .card--back  { top: 607px; border-radius: 62px 0 62px 0; }

  .faint-mark {
    position: absolute;
    left: -40px; top: 70px;
    width: 210px; height: 210px;
    background: var(--faint);
    transform: rotate(45deg);
  }
  .brand {
    position: absolute;
    display: flex;
    align-items: center;
    gap: 14px;
    font-weight: 700;
    color: var(--ink);
    letter-spacing: -0.5px;
  }
  .brand__square {
    width: 40px; height: 40px;
    background: var(--brand-red);
    transform: rotate(45deg);
    margin: 0 8px;
  }
  .card--front .brand { right: 42px; top: 56px; font-size: 52px; }
  .card--back .brand { left: 0; right: 0; justify-content: center; top: 117px; font-size: 52px; }

  .person { position: absolute; left: 49px; top: 182px; }
  .person__name { color: var(--brand-red); font-weight: 700; font-size: 19px; }
  .person__role { font-size: 16px; margin-top: 3px; }

  .contacts { position: absolute; left: 48px; top: 239px; list-style: none; font-size: 16px; line-height: 21px; }
  .contacts li { display: flex; align-items: center; gap: 4px; }
  .contacts svg { width: 12px; height: 12px; fill: var(--brand-red); }

  .address { position: absolute; right: 35px; top: 282px; text-align: right; font-size: 16px; line-height: 21px; }

  .rule { position: absolute; left: 70px; right: 79px; top: 245px; border-top: 1px solid var(--rule); }
  .services { position: absolute; left: 0; right: 0; top: 268px; display: flex; justify-content: center; gap: 16px; font-size: 26px; font-weight: 700; letter-spacing: -0.5px; }
  .service { display: flex; align-items: center; gap: 10px; }
  .service__square { width: 20px; height: 20px; transform: rotate(45deg); }
  .service--ship { color: var(--ship-blue); }
  .service--ship .service__square { background: var(--ship-blue); }
  .service--keep { color: var(--keep-magenta); }
  .service--keep .service__square { background: var(--keep-magenta); }
  .service--map { color: var(--map-green); }
  .service--map .service__square { background: var(--map-green); }
</style>
</head>
<body>
  <section class="card card--front">
    <div class="faint-mark" aria-hidden="true"></div>
    <div class="brand"><span class="brand__square"></span>korvalIT</div>
    <div class="person">
      <p class="person__name">Marcus Hale</p>
      <p class="person__role">Position</p>
    </div>
    <ul class="contacts">
      <li><svg viewBox="0 0 12 12"><path d="M3 0h6a1 1 0 0 1 1 1v10a1 1 0 0 1-1 1H3a1 1 0 0 1-1-1V1a1 1 0 0 1 1-1zm0 2v7h6V2z"/></svg>412 308 55921</li>
      <li><svg viewBox="0 0 12 12"><path d="M0 4c0-2 2-3 6-3s6 1 6 3v1H9V4H3v1H0zM2 6h8l1 5H1z"/></svg>412 308 55921</li>
      <li><svg viewBox="0 0 12 12"><path d="M0 2h12v8H0zM1 3l5 4 5-4"/></svg>info@korvalit.com.au</li>
      <li><svg viewBox="0 0 12 12"><circle cx="6" cy="6" r="6"/></svg>www.korvalit.com.au</li>
    </ul>
    <address class="address" style="font-style:normal">Level 1, 47 Fernby Street<br>Carlow Qld 4072</address>
  </section>

  <section class="card card--back">
    <div class="brand"><span class="brand__square"></span>korvalIT</div>
    <div class="rule"></div>
    <div class="services">
      <span class="service service--ship"><span class="service__square"></span>ShipWell</span>
      <span class="service service--keep"><span class="service__square"></span>KeepSteady</span>
      <span class="service service--map"><span class="service__square"></span>MapOut</span>
    </div>
  </section>
</body>
</html>
```